A website for a Maltese Law Firm

Our law firm needs a website to further its business. The site should have a simple yet effective design. We would need the following sections: About us, Practice Areas, About Malta, Contact. These should be further split as follows:

About us: Our firm, Our values, What others say, Offices

Practice Areas: Crimimal, Citizenship & Residence, Sovereign Patron Pathway, Criminal Defence, Civil Litigation, Arbitration and ADR, Commercial and Corporate, Media Law.

About Malta: just one section.

Contact: Just one section

We would also need a news feed at the front of the site to include latest news regarding our cases.

At the bottom we need a section for our Terms and a Privacy Statement.

Our logo is being attached.

Target Market(s)

All clients looking for legal assistance in Malta

Industry/Entity Type

Legal

Coding

Coded - Design and coding required

Number of Pages Required

1 page

Requirements
Must have
• It must be simple yet striking.

```html
<!DOCTYPE html>
<html lang="en">
<head>
<meta charset="utf-8">
<title>Calleja &amp; Sant Advocates</title>
<link rel="stylesheet" href="https://fonts.googleapis.com/css2?family=Cinzel:wght@400;700&family=Lato:wght@400;700&display=swap">
<style>
:root{
  --black:#161616;
  --black-2:#1d1d1d;
  --white:#ffffff;
  --light:#e8e8e6;
  --card:#e9e9e9;
  --news-bg:#e4e4e4;
  --text:#222222;
  --muted:#bdbdbd;
  --rule:#9a9a9a;
  --heading:"Cinzel", serif;
  --body:"Lato", sans-serif;
}
*{margin:0;padding:0;box-sizing:border-box}
html,body{width:1200px;height:2590px;overflow:hidden}
body{font-family:var(--body);color:var(--text);background:var(--white);position:relative}
.wrap{position:absolute;left:98px;width:1004px}

/* header */
.site-header{position:absolute;top:0;left:0;width:1200px;height:98px;background:var(--black)}
.brand{position:absolute;left:98px;top:26px;color:var(--white);font-family:var(--heading);font-weight:400;text-align:center}
.brand-name{font-size:25px;letter-spacing:1px;line-height:30px}
.brand-sub{font-size:11px;letter-spacing:4px;line-height:14px}
.header-phone{position:absolute;right:98px;top:14px;color:var(--white);font-family:var(--heading);font-size:18px;display:flex;align-items:center;gap:10px}
.main-nav{position:absolute;right:98px;top:66px;display:flex;font-family:var(--heading);font-size:13px;color:var(--white)}
.main-nav span{padding:0 12px}
.main-nav span.sep{padding:0;color:#aaa}
.main-nav span:last-child{padding-right:0}

/* hero */
.hero{position:absolute;top:98px;left:0;width:1200px;height:515px;background:radial-gradient(ellipse at 40% 70%,#6b4429 0%,#3a2416 45%,#1d130c 100%);border-top:3px solid #888}
.hero-title{position:absolute;top:200px;width:1200px;text-align:center;color:var(--white);font-family:var(--heading);font-size:30px;line-height:46px;letter-spacing:1px}
.hero-btn{position:absolute;left:493px;top:308px;width:214px;height:37px;background:var(--white);border-radius:3px;font-size:15px;font-weight:700;color:var(--black);display:flex;align-items:center;justify-content:center}
.hero-arrow{position:absolute;top:237px}

/* about */
.about{position:absolute;top:613px;left:0;width:1200px;height:404px;background:var(--light)}
.about-photo{position:absolute;left:98px;top:52px;width:296px;height:287px;background:#d5d5d3;padding:16px}
.about-photo div{width:100%;height:100%;background:linear-gradient(160deg,#8a8a8a,#4a4a4a 60%,#1f1f1f)}
.about-body{position:absolute;left:440px;top:44px;width:662px}
.section-title{font-family:var(--heading);font-size:32px;color:var(--black);letter-spacing:1px;line-height:42px}
.title-rule{height:1px;background:var(--rule);margin-top:4px;position:relative}
.title-rule::before{content:"";position:absolute;left:0;top:-1px;height:3px;background:var(--black)}
.about .title-rule{width:488px}
.about .title-rule::before{width:128px}
.about p{font-size:13.5px;line-height:24px;margin-top:22px}
.about-links{display:flex;gap:40px;margin-top:18px;font-size:14px;font-weight:700}
.about-links span::before{content:"";display:inline-block;width:8px;height:8px;border-radius:50%;background:#333;margin-right:14px;vertical-align:middle}
.btn-dark{display:inline-flex;align-items:center;justify-content:center;width:110px;height:34px;background:var(--black);color:var(--white);font-size:13px;margin-top:20px}

/* practice */
.practice{position:absolute;top:1017px;left:0;width:1200px;height:501px;background:var(--white)}
.center-title{position:absolute;top:40px;width:1200px;text-align:center}
.center-title .section-title{display:inline-block}
.center-rule{width:352px;margin:4px auto 0}
.center-rule::before{left:112px!important;width:128px}
.practice-intro{position:absolute;top:113px;width:1200px;text-align:center;font-size:13.5px}
.practice-cards{top:157px;display:flex;gap:38px}
.practice-card{width:309px;height:297px;background:var(--card);border-bottom:3px solid var(--black);position:relative;text-align:center}
.practice-card .img{height:142px}
.icon-badge{position:absolute;left:122px;top:118px;width:64px;height:64px;border-radius:50%;background:var(--card);display:flex;align-items:center;justify-content:center}
.practice-card h3{font-family:var(--heading);font-size:18px;font-weight:400;margin-top:46px;letter-spacing:.5px}
.practice-card p{font-size:13px;line-height:19px;color:#444;margin:14px 30px 0}
.side-arrow{position:absolute;top:1320px}

/* malta */
.malta{position:absolute;top:1518px;left:0;width:1200px;height:312px;background:var(--black)}
.malta .section-title{color:var(--white);position:absolute;left:98px;top:36px}
.malta .title-rule{position:absolute;left:98px;top:86px;width:230px;background:#555}
.malta .title-rule::before{background:var(--white);width:0}
.malta p{position:absolute;left:98px;top:104px;width:600px;font-size:13.5px;line-height:23px;color:var(--white)}
.btn-outline{position:absolute;left:98px;top:236px;width:113px;height:34px;border:1px solid var(--white);color:var(--white);font-size:13px;display:flex;align-items:center;justify-content:center}
.malta-img{position:absolute;left:775px;top:57px;width:327px;height:190px;border:2px solid #8aa;background:linear-gradient(180deg,#2d3e6e 0%,#5a4a6a 40%,#c9762c 62%,#3a3a7a 78%,#1c2a55 100%)}

/* news */
.news{position:absolute;top:1830px;left:0;width:1200px;height:467px;background:var(--news-bg)}
.news .center-title{top:38px}
.news-cards{top:116px;display:flex;gap:33px}
.news-card{width:309px}
.news-card .img{height:196px;position:relative}
.news-date{position:absolute;right:18px;top:12px;background:var(--black);color:var(--white);font-size:13px;padding:5px 14px}
.news-card h4{font-size:14.5px;font-weight:700;margin-top:17px;color:var(--black)}
.news-card p{font-size:13px;line-height:19px;margin-top:14px;color:#333}

/* footer */
.site-footer{position:absolute;top:2297px;left:0;width:1200px;height:250px;background:var(--black-2);color:var(--white)}
.footer-col{position:absolute;top:44px}
.footer-col h5{font-family:var(--heading);font-weight:400;font-size:18px;letter-spacing:1px}
.footer-col .rule{height:1px;background:#444;margin-top:8px}
.footer-divider{position:absolute;top:40px;width:1px;height:170px;background:#333}
.quick-links{list-style:none;margin-top:18px;font-size:13px;line-height:27.5px}
.quick-links li::before{content:"›";color:#999;margin-right:10px}
.contact-list{list-style:none;margin-top:20px;font-size:13px;color:#ddd}
.contact-list li{display:flex;gap:12px;margin-bottom:12px;line-height:18px}
.contact-list svg{flex:none;margin-top:2px}
.footer-map{position:absolute;left:568px;top:92px;width:263px;height:138px;border:3px solid var(--white);background:linear-gradient(135deg,#ece7dc,#dfe6d8 50%,#e9e4d6)}
.footer-brand{position:absolute;left:903px;top:118px;width:199px;text-align:center;font-family:var(--heading)}
.footer-brand .brand-name{font-size:18px;line-height:22px}
.footer-brand .brand-sub{font-size:8px;letter-spacing:3px}
.social{display:flex;justify-content:center;gap:8px;margin-top:16px}
.social span{width:24px;height:24px;border-radius:50%}
.copyright{position:absolute;top:2547px;left:0;width:1200px;height:43px;background:#101010;color:#ccc;font-size:13px;display:flex;align-items:center;justify-content:center}
</style>
</head>
<body>

<header class="site-header">
  <div class="brand">
    <div class="brand-name">CALLEJA &amp; SANT</div>
    <div class="brand-sub">ADVOCATES</div>
  </div>
  <div class="header-phone">
    <svg width="28" height="28" viewBox="0 0 28 28"><circle cx="14" cy="14" r="12.5" fill="none" stroke="#fff" stroke-width="2"/><path d="M10 8c1 0 2 2.5 2 3s-1 1-1 1.5 2.5 3.5 4 4 1-1 1.5-1 3 1 3 2-1.5 2-2.5 2c-4 0-9-5-9-9 0-1 1-3.5 2-3.5z" fill="#fff"/></svg>
    <span>CALL: (713)-555-0147</span>
  </div>
  <nav class="main-nav">
    <span>HOME</span><span class="sep">|</span><span>ABOUT US</span><span class="sep">|</span><span>PRACTICE AREAS</span><span class="sep">|</span><span>ABOUT MALTA</span><span class="sep">|</span><span>CONTACT US</span>
  </nav>
</header>

<section class="hero" role="img" aria-label="Law books, handcuffs and a judge's gavel on a wooden desk">
  <svg class="hero-arrow" style="left:42px" width="38" height="38" viewBox="0 0 38 38"><circle cx="19" cy="19" r="17" fill="none" stroke="#fff" stroke-width="2"/><path d="M22 12l-7 7 7 7" fill="none" stroke="#fff" stroke-width="2"/></svg>
  <svg class="hero-arrow" style="right:42px" width="38" height="38" viewBox="0 0 38 38"><circle cx="19" cy="19" r="17" fill="none" stroke="#fff" stroke-width="2"/><path d="M16 12l7 7-7 7" fill="none" stroke="#fff" stroke-width="2"/></svg>
  <h1 class="hero-title" style="font-weight:400">THE GREATEST AND STRONGEST<br>FIRM YOU CAN TRUST</h1>
  <div class="hero-btn">Request A Free Consult</div>
</section>

<section class="about">
  <div class="about-photo"><div role="img" aria-label="Portrait photograph of a lawyer in a suit"></div></div>
  <div class="about-body">
    <h2 class="section-title" style="font-weight:400">ABOUT CALLEJA &amp; SANT</h2>
    <div class="title-rule"></div>
    <p>Lorem ipsum dolor sit amet, consectetuer adipiscing elit, sed diam nonummy nibh euismod tincidunt ut laoreet dolore magna aliquam erat volutpat. Ut wisi enim ad minim veniam, quis nostrud exerci tation ullamcorper suscipit lobortis nisl ut aliquip ex ea commodo consequat. Duis autem vel eum iriure dolor in hendrerit in vulputate velit esse molestie consequat, vel illum dolore eu feugiat nulla facilisis at vero eros et accumsan et iusto odio dignissim qui blandit praesent luptatum zzril delenit augue duis dolore te feugait nulla facilisi.</p>
    <div class="about-links"><span>Our Firms</span><span>Our Values</span></div>
    <div class="btn-dark">Read More</div>
  </div>
</section>

<section class="practice">
  <div class="center-title">
    <h2 class="section-title" style="font-weight:400">OUR PRACTICE AREAS</h2>
    <div class="title-rule center-rule"></div>
  </div>
  <p class="practice-intro">Lorem ipsum dolor sit amet, consectetur adipisicing elit. Obcaecati laborum ipsa, a voluptates libero possimus sapiente.</p>
  <div class="wrap practice-cards">
    <article class="practice-card">
      <div class="img" role="img" aria-label="Law books with scales of justice and a gavel" style="background:linear-gradient(135deg,#5a3a22,#a8875a 55%,#3b2616)"></div>
      <div class="icon-badge"><svg width="30" height="24" viewBox="0 0 30 24"><circle cx="8" cy="15" r="6" fill="none" stroke="#111" stroke-width="2.5"/><circle cx="22" cy="15" r="6" fill="none" stroke="#111" stroke-width="2.5"/><path d="M10 9l3-5h4l3 5" fill="none" stroke="#111" stroke-width="2"/></svg></div>
      <h3>CRMINAL LAW</h3>
      <p>Sed ut perspiciatis unde omnis iste natus error sit voluptatem accusantium omnis unde doloremque laudantium</p>
    </article>
    <article class="practice-card">
      <div class="img" role="img" aria-label="Passports resting on a world map" style="background:linear-gradient(135deg,#d9d2c4,#7a2a2a 55%,#2a2540)"></div>
      <div class="icon-badge"><svg width="26" height="24" viewBox="0 0 26 24"><path d="M13 2L1 13h4v10h6v-7h4v7h6V13h4z" fill="#111"/></svg></div>
      <h3>CITIZENSHIP AND RESIDENCE</h3>
      <p>Sed ut perspiciatis unde omnis iste natus error sit voluptatem accusantium omnis unde doloremque laudantium</p>
    </article>
    <article class="practice-card">
      <div class="img" role="img" aria-label="Columned court building under a blue sky" style="background:linear-gradient(180deg,#2d4f9a,#8aa0c8 45%,#d8d4c8 70%,#6c6a64)"></div>
      <div class="icon-badge"><svg width="26" height="24" viewBox="0 0 26 24"><path d="M13 1L1 7h24z" fill="#111"/><rect x="3" y="9" width="3" height="10" fill="#111"/><rect x="9" y="9" width="3" height="10" fill="#111"/><rect x="15" y="9" width="3" height="10" fill="#111"/><rect x="21" y="9" width="3" height="10" fill="#111"/><rect x="1" y="20" width="24" height="3" fill="#111"/></svg></div>
      <h3>CIVIL LITIGATION</h3>
      <p>Sed ut perspiciatis unde omnis iste natus error sit voluptatem accusantium omnis unde doloremque laudantium</p>
    </article>
  </div>
  <svg class="side-arrow" style="left:52px;top:303px" width="20" height="36" viewBox="0 0 20 36"><path d="M18 2L3 18l15 16" fill="none" stroke="#555" stroke-width="2"/></svg>
  <svg class="side-arrow" style="right:52px;top:303px" width="20" height="36" viewBox="0 0 20 36"><path d="M2 2l15 16L2 34" fill="none" stroke="#555" stroke-width="2"/></svg>
</section>

<section class="malta">
  <h2 class="section-title" style="font-weight:400">ABOUT MALTA</h2>
  <div class="title-rule"></div>
  <p>Lorem ipsum dolor sit amet, consectetur adipisicing elit, sed do eiusmod tempor incididunt ut labore et dolore magna aliqua. Ut enim ad minim veniam, quis nostrud exercitation ullamco laboris nisi ut aliquip ex ea commodo consequat. Duis aute irure dolor in reprehenderit in voluptate velit esse cillum dolore eu fugiat nulla pariatur. Excepteur sint occaecat cupidatat non proident, sunt in culpa qui officia deserunt mollit anim id est laborum.</p>
  <div class="btn-outline">Read More</div>
  <div class="malta-img" role="img" aria-label="Valletta harbour skyline lit at dusk"></div>
</section>

<section class="news">
  <div class="center-title">
    <h2 class="section-title" style="font-weight:400">LATEST NEWS</h2>
    <div class="title-rule center-rule" style="width:250px"></div>
  </div>
  <div class="wrap news-cards">
    <article class="news-card">
      <div class="img" role="img" aria-label="Lawyer signing a document at a desk" style="background:linear-gradient(135deg,#2a2a2a,#5a4a3a 60%,#8a6a4a)"><span class="news-date">08, June</span></div>
      <h4>We denounce with righteous indignation and.</h4>
      <p>At vero eos et accusamus et iusto odio dignissimos ducimus qui blanditiis praesentium voluptatum deleniti atque corrupti quos dolores et.</p>
    </article>
    <article class="news-card">
      <div class="img" role="img" aria-label="Brass scales of justice on a courtroom table" style="background:linear-gradient(135deg,#c98a4a,#7a4a24 55%,#3a2414)"><span class="news-date">08, June</span></div>
      <h4>We denounce with righteous indignation and.</h4>
      <p>At vero eos et accusamus et iusto odio dignissimos ducimus qui blanditiis praesentium voluptatum deleniti atque corrupti quos dolores et.</p>
    </article>
    <article class="news-card">
      <div class="img" role="img" aria-label="White stone columns of a court building" style="background:linear-gradient(90deg,#f2f2f0,#9a9a98 35%,#e8e8e6 60%,#6a6a68)"><span class="news-date">08, June</span></div>
      <h4>We denounce with righteous indignation and.</h4>
      <p>At vero eos et accusamus et iusto odio dignissimos ducimus qui blanditiis praesentium voluptatum deleniti atque corrupti quos dolores et.</p>
    </article>
  </div>
</section>

<footer class="site-footer">
  <div class="footer-col" style="left:98px;width:130px">
    <h5>QUICK LINKS</h5><div class="rule"></div>
    <ul class="quick-links"><li>Home</li><li>About Us</li><li>Practice Areas</li><li>About Malta</li><li>Contact Us</li></ul>
  </div>
  <div class="footer-divider" style="left:254px"></div>
  <div class="footer-col" style="left:288px;width:205px">
    <h5>CONTACT DETAIL</h5><div class="rule"></div>
    <ul class="contact-list">
      <li><svg width="12" height="16" viewBox="0 0 12 16"><path d="M6 0a6 6 0 0 0-6 6c0 4 6 10 6 10s6-6 6-10a6 6 0 0 0-6-6zm0 8.5A2.5 2.5 0 1 1 6 3.5a2.5 2.5 0 0 1 0 5z" fill="#fff"/></svg><span>12/4, Harbour Lane, Valletta<br>88, Olive Street, Birkirkara</span></li>
      <li><svg width="12" height="12" viewBox="0 0 12 12"><path d="M3 0c1 0 2 2.5 2 3s-1 1-1 1.5 2 3 3.5 3.5 1-1 1.5-1 3 1 3 2-1.5 2-2.5 2C4 11 1 7 1 3c0-1 1-3 2-3z" fill="#fff"/></svg><span>(713) -555 - 0147</span></li>
      <li><svg width="13" height="12" viewBox="0 0 13 12"><rect x="3" y="0" width="7" height="3" fill="#fff"/><rect x="0" y="4" width="13" height="5" rx="1" fill="#fff"/><rect x="3" y="8" width="7" height="4" fill="#fff"/></svg><span>(713) -555 - 0182</span></li>
      <li><svg width="13" height="10" viewBox="0 0 13 10"><rect width="13" height="10" fill="#fff"/><path d="M0 0l6.5 5L13 0" fill="none" stroke="#1d1d1d" stroke-width="1.2"/></svg><span>info@csadvocates.example</span></li>
    </ul>
  </div>
  <div class="footer-divider" style="left:527px"></div>
  <div class="footer-col" style="left:568px;width:263px">
    <h5>LOCATION MAP</h5><div class="rule"></div>
  </div>
  <div class="footer-map" role="img" aria-label="Street map showing the office location"></div>
  <div class="footer-divider" style="left:865px"></div>
  <div class="footer-brand">
    <div class="brand-name">CALLEJA &amp; SANT</div>
    <div class="brand-sub">ADVOCATES</div>
    <div class="social"><span style="background:#3b5998"></span><span style="background:#1da1f2"></span><span style="background:#0077b5"></span><span style="background:#d34836"></span></div>
  </div>
</footer>
<div class="copyright">Copyright © 2016 - Calleja &amp; Sant Advocates, All Rights Reserved.</div>

</body>
</html>
```